BrindleStaffing Business Card Design

We are a staffing company finding positions for dedicated nurses and physicians.

Target Market(s)

Business Professionals

Industry/Entity Type

Staffing

Contact Information for Business Card

Gordon Pratley
Chairman
417 39th Avenue South
SAINT PETERSBURG FL 33712
813-555-4172 Mobile
813-555-8036 Fax
gpratley@brindlestaffing.com
www.brindlestaffing.com

Font styles to use
Sans Serif

Colors
fbee3e
f04a50
f37122

Requirements
Must have
• Logo Attached, see colors below. We'd like to see Yellow, Orange and Red.

```html
<!DOCTYPE html>
<html lang="en">
<head>
<meta charset="utf-8">
<title>BrindleStaffing Business Card</title>
<link rel="stylesheet" href="https://fonts.googleapis.com/css2?family=PT+Sans:wght@400;700&display=swap">
<style>
  :root {
    --stage: #ecebe8;
    --card-white: #ffffff;
    --brand-yellow: #fbee3e;
    --brand-orange: #f37122;
    --brand-red: #f04a50;
    --ink: #4a4a4a;
    --rule: #9a9a9a;
  }
  * { margin: 0; padding: 0; box-sizing: border-box; }
  html, body {
    width: 1200px; height: 768px; overflow: hidden;
    background: var(--stage);
    font-family: "PT Sans", Arial, sans-serif;
  }
  .stage {
    position: relative; width: 1200px; height: 768px;
    display: flex; align-items: center; justify-content: center; gap: 40px;
  }
  .card {
    position: relative; width: 540px; height: 310px;
    border-radius: 22px; overflow: hidden;
    box-shadow: 0 10px 28px rgba(0,0,0,.18);
  }
  .card-front { background: var(--card-white); }
  .card-back {
    background: var(--brand-orange);
    display: flex; align-items: center; justify-content: center;
  }
  .wordmark { font-weight: 700; letter-spacing: -1px; line-height: 1; }
  .card-front .wordmark {
    position: absolute; top: 62px; left: 0; right: 0; text-align: center;
    font-size: 56px; color: var(--brand-orange);
  }
  .card-back .wordmark { font-size: 62px; color: var(--card-white); }
  .holder { position: absolute; left: 34px; top: 172px; }
  .holder-name { font-weight: 700; font-size: 24px; color: var(--brand-red); }
  .holder-title { font-size: 15px; color: var(--brand-orange); margin-top: -2px; }
  .divider {
    position: absolute; left: 34px; right: 34px; top: 226px;
    height: 1px; background: var(--rule);
  }
  .contact {
    position: absolute; top: 238px; left: 34px; right: 34px;
    display: flex; justify-content: space-between;
    font-size: 12.5px; color: var(--ink); line-height: 1.45;
  }
  .contact-line { display: flex; align-items: center; gap: 6px; }
  .contact-line svg { width: 11px; height: 11px; flex: none; }
  .edge-band {
    position: absolute; left: 0; right: 0; bottom: 0; height: 14px;
    background: var(--brand-red);
  }
  .edge-accent {
    position: absolute; left: 0; bottom: 0; width: 44px; height: 14px;
    background: var(--brand-yellow);
  }
</style>
</head>
<body>
<main class="stage">
  <section class="card card-front">
    <div class="wordmark">BrindleStaffing</div>

    <div class="holder">
      <div class="holder-name">Gordon Pratley</div>
      <div class="holder-title">Chairman</div>
    </div>

    <div class="divider"></div>

    <div class="contact">
      <div class="contact-address">
        <div>417 39th Avenue South</div>
        <div>Saint Petersburg Fl 33712</div>
      </div>
      <div class="contact-phones">
        <div class="contact-line">
          <svg viewBox="0 0 12 12"><rect x="3" y="0.5" width="6" height="11" rx="1.2" fill="none" stroke="var(--brand-red)" stroke-width="1.3"/></svg>
          813-555-4172
        </div>
        <div class="contact-line">
          <svg viewBox="0 0 12 12"><rect x="1" y="4" width="10" height="7" rx="1" fill="var(--brand-red)"/><rect x="3" y="1" width="6" height="3" fill="none" stroke="var(--brand-red)"/></svg>
          813-555-8036
        </div>
      </div>
      <div class="contact-web">
        <div class="contact-line">
          <svg viewBox="0 0 12 12"><rect x="0.5" y="2" width="11" height="8" fill="var(--brand-red)"/><path d="M0.5 2 6 7 11.5 2" fill="none" stroke="#fff" stroke-width="1"/></svg>
          gpratley@brindlestaffing.com
        </div>
        <div class="contact-line">
          <svg viewBox="0 0 12 12"><circle cx="6" cy="6" r="5.5" fill="var(--brand-red)"/><path d="M0.5 6h11M6 0.5c-2.5 3-2.5 8 0 11M6 0.5c2.5 3 2.5 8 0 11" fill="none" stroke="#fff" stroke-width=".8"/></svg>
          www.brindlestaffing.com
        </div>
      </div>
    </div>

    <div class="edge-band"></div>
    <div class="edge-accent"></div>
  </section>

  <section class="card card-back">
    <div class="wordmark">BrindleStaffing</div>
  </section>
</main>
</body>
</html>
```